Varentoria Business Card and Letter Head

We are a leadership assessment consultancy based in Sydney, Australia. We help executive-level decison-makers select leaders for more senior level roles in corporate and government organisations. Our methodology is based on the latest research from the field of neuroscience.
We need a business card design and matching letter head that presents our company, Varentoria, as a:
1. trusted adviser to senior executive-level decison makers
2. niche consultancy who are experts in the field of assessing leadership talent
3. results-focused solution provider who balance scientific methods with pragmatic solutions
The following company details should be used in all designs:
Company Name: Varentoria
Details (for business card):
Derek Hanford
Prime Capacity Officer
Level 29, Marlow Tower
7 Marlow Square
Sydney, NSW 2000 Australia
Phone: 1300 582 714
Mobile: 0412 637 258
Email: derek.hanford@varentoria-example.com.au
Website: varentoria-example.com.au
I have attached the logo for Varentoria (for both a white and black background) - your business card and letter head designs must incoporate this logo and colour scheme.
Thanks for your interest in this project, I'm looking forward to receiving your ideas.
Regards,
Derek
Target Market(s)
Executive-level decison-makers in corporate and government organisations (e.g., CEO, VP, Head of Human Resources)
Industry/Entity Type
Leadership
Look and feel

```html
<!DOCTYPE html>
<html lang="en">
<head>
<meta charset="utf-8">
<title>Varentoria Business Card</title>
<link href="https://fonts.googleapis.com/css2?family=Open+Sans:wght@400;600;700&display=swap" rel="stylesheet">
<style>
  :root {
    --backdrop: #e8e4dd;
    --card-white: #ffffff;
    --card-dark: #404040;
    --brand-red: #c1281b;
    --band-grey: #3d3d3d;
    --ink: #3a3a3a;
    --ink-soft: #5a5a5a;
    --on-dark: #ffffff;
  }
  * { box-sizing: border-box; margin: 0; padding: 0; }
  html, body { width: 1200px; height: 469px; overflow: hidden; }
  body {
    background: var(--backdrop);
    font-family: "Open Sans", Arial, sans-serif;
    position: relative;
  }
  .card {
    position: absolute;
    top: 83px;
    width: 527px;
    height: 299px;
    border-radius: 14px;
    overflow: hidden;
    box-shadow: 0 3px 8px rgba(0,0,0,0.25);
  }
  .card--front { left: 44px; background: var(--card-white); }
  .card--back { left: 620px; background: var(--card-dark); }

  .front-waves { position: absolute; left: 0; top: 0; width: 527px; height: 299px; }

  .brand {
    position: absolute;
    display: flex;
    align-items: center;
    gap: 12px;
  }
  .brand__mark { width: 16px; height: 16px; flex: none; }
  .brand__name {
    font-weight: 700;
    font-size: 38px;
    line-height: 1;
    letter-spacing: -0.6px;
  }
  .brand__tagline {
    font-size: 10.5px;
    letter-spacing: 1.1px;
    margin-top: 5px;
    white-space: nowrap;
  }
  .card--front .brand { left: 160px; top: 62px; }
  .card--front .brand__mark { background: var(--brand-red); }
  .card--front .brand__name { color: var(--ink); }
  .card--front .brand__tagline { color: var(--ink-soft); }

  .card--back .brand { left: 179px; top: 104px; }
  .card--back .brand__mark { background: var(--on-dark); }
  .card--back .brand__name, .card--back .brand__tagline { color: var(--on-dark); }
  .back-web {
    position: absolute;
    left: 209px; top: 171px;
    color: var(--on-dark);
    font-size: 13.5px;
    letter-spacing: 0.8px;
  }

  .holder {
    position: absolute;
    left: 22px; top: 247px;
    color: var(--on-dark);
  }
  .holder__name { font-weight: 700; font-size: 14px; line-height: 1.2; }
  .holder__title { font-size: 11px; line-height: 1.3; }
  .divider {
    position: absolute;
    left: 145px; top: 225px;
    width: 1px; height: 50px;
    background: rgba(255,255,255,0.7);
  }
  .contact {
    position: absolute;
    left: 154px; top: 224px;
    color: var(--on-dark);
    font-size: 11px;
    line-height: 16px;
  }
  .contact__grid {
    display: grid;
    grid-template-columns: 102px auto;
    margin-top: 6px;
  }
  .contact__item { display: flex; align-items: center; gap: 6px; white-space: nowrap; }
  .contact__icon { width: 10px; height: 10px; flex: none; }
</style>
</head>
<body>
  <section class="card card--front">
    <svg class="front-waves" viewBox="0 0 527 299" aria-hidden="true">
      <path d="M0,148 C130,150 230,190 350,180 C430,174 490,172 527,178 L527,190 C480,184 420,186 350,194 C230,204 120,170 0,168 Z" fill="var(--band-grey)"/>
      <path d="M0,170 C130,176 240,210 360,198 C440,190 495,186 527,190 L527,299 L0,299 Z" fill="var(--brand-red)"/>
    </svg>

    <div class="brand">
      <span class="brand__mark"></span>
      <div>
        <div class="brand__name">Varentoria</div>
        <div class="brand__tagline">ASSESSING EXECUTIVE POTENTIAL</div>
      </div>
    </div>

    <div class="holder">
      <div class="holder__name">Derek Hanford</div>
      <div class="holder__title">Prime Capacity Officer</div>
    </div>
    <div class="divider"></div>

    <div class="contact">
      <div class="contact__address">Level 29, Marlow Tower 7 Marlow Square Sydney, NSW 2000 Australia</div>
      <div class="contact__grid">
        <div class="contact__item">
          <svg class="contact__icon" viewBox="0 0 10 10" aria-hidden="true"><path d="M2,0.5 L3.8,2.8 L2.8,4 C3.4,5.4 4.6,6.6 6,7.2 L7.2,6.2 L9.5,8 L8,9.5 C4,9 1,6 0.5,2 Z" fill="#fff"/></svg>
          <span>1300 582 714</span>
        </div>
        <div class="contact__item">
          <svg class="contact__icon" viewBox="0 0 10 10" aria-hidden="true"><rect x="1.5" y="1.5" width="7" height="5" fill="#fff"/><path d="M1.5,1.5 L5,4.5 L8.5,1.5" stroke="var(--brand-red)" stroke-width="0.8" fill="none"/></svg>
          <span>derek.hanford@varentoria-example.com.au</span>
        </div>
        <div class="contact__item">
          <svg class="contact__icon" viewBox="0 0 10 10" aria-hidden="true"><rect x="2.5" y="0.5" width="5" height="9" rx="1" fill="#fff"/><rect x="3.4" y="1.6" width="3.2" height="4" fill="var(--brand-red)"/></svg>
          <span>0412 637 258</span>
        </div>
        <div class="contact__item">
          <svg class="contact__icon" viewBox="0 0 10 10" aria-hidden="true"><circle cx="5" cy="5" r="4.5" fill="#fff"/><path d="M0.5,5 H9.5 M5,0.5 C2.5,3 2.5,7 5,9.5 M5,0.5 C7.5,3 7.5,7 5,9.5" stroke="var(--brand-red)" stroke-width="0.7" fill="none"/></svg>
          <span>www.varentoria-example.com.au</span>
        </div>
      </div>
    </div>
  </section>

  <section class="card card--back">
    <div class="brand">
      <span class="brand__mark"></span>
      <div>
        <div class="brand__name">Varentoria</div>
        <div class="brand__tagline">ASSESSING EXECUTIVE POTENTIAL</div>
      </div>
    </div>
    <div class="back-web">www.varentoria-example.com.au</div>
  </section>
</body>
</html>
```